KRT Project Signage

Need a sign to be displayed in the front of properties currently under Construction or Renovation to advertise our company information. Need it to be Professional and Contemporary. We are a Design/Build Construction Company. Information should include Company Name, email, website, phone number. Attached: Logo and company brochure, also included and inspiration images

```html
<!DOCTYPE html>
<html lang="en">
<head>
<meta charset="utf-8">
<title>KRT Project Signage</title>
<link rel="stylesheet" href="https://fonts.googleapis.com/css2?family=Federo&family=Poppins:wght@400;500;700&display=swap">
<style>
  :root {
    --backdrop: #9aa1a8;
    --sign-yellow: #f2eb48;
    --sign-black: #000000;
    --sign-white: #ffffff;
    --ink-navy: #0f1e2e;
  }
  html, body {
    margin: 0;
    padding: 0;
    width: 1200px;
    height: 2400px;
    overflow: hidden;
    background: var(--backdrop);
  }
  .project-sign {
    position: absolute;
    left: 100px;
    top: 450px;
    width: 1000px;
    height: 1499px;
    box-shadow: 0 18px 40px rgba(0, 0, 0, 0.35);
  }
  .project-sign svg { display: block; width: 100%; height: 100%; }
  .fill-yellow { fill: var(--sign-yellow); }
  .fill-black { fill: var(--sign-black); }
  .fill-white { fill: var(--sign-white); }
  .fill-navy { fill: var(--ink-navy); }
  .display-type { font-family: "Federo", sans-serif; }
  .body-type { font-family: "Poppins", sans-serif; }
  .brand-name { font-size: 44px; fill: var(--ink-navy); }
  .owner-name { font-size: 112px; fill: var(--ink-navy); }
  .tagline { font-size: 44px; letter-spacing: 14px; fill: var(--ink-navy); }
  .address-line { font-size: 35px; font-weight: 500; fill: var(--sign-white); }
  .email-line { font-size: 38px; font-weight: 500; fill: var(--sign-white); }
  .office-label { font-size: 42px; font-weight: 700; fill: var(--sign-black); letter-spacing: 2px; }
  .office-number { font-size: 54px; font-weight: 700; fill: var(--sign-black); }
  .mobile-number { font-size: 92px; font-weight: 700; fill: var(--sign-white); }
</style>
</head>
<body>
  <main class="project-sign">
    <svg viewBox="0 0 778 1166" xmlns="http://www.w3.org/2000/svg">
      <!-- base -->
      <rect class="fill-yellow" x="0" y="0" width="778" height="1166"/>

      <!-- header dome with crescent -->
      <path class="fill-black" d="M54 60 C66 285 232 378 392 378 C560 378 716 285 724 60 C702 252 560 344 390 344 C220 344 76 252 54 60 Z"/>
      <path class="fill-white" d="M58 0 L720 0 C720 200 560 327 390 327 C220 327 58 200 58 0 Z" stroke="var(--sign-yellow)" stroke-width="8"/>

      <!-- brand -->
      <text class="display-type brand-name" x="350" y="157" text-anchor="middle">KRT CONSTRUCTION</text>
      <circle class="brand-dot" cx="605" cy="141" r="26" fill="var(--sign-yellow)"/>

      <!-- owner name -->
      <text class="display-type owner-name" x="60" y="505" textLength="662" lengthAdjust="spacingAndGlyphs">MARCUS DELANE</text>

      <!-- contact panel -->
      <path class="fill-black" d="M0 780 C100 640 250 575 400 575 C560 575 700 650 778 735 L778 1166 L0 1166 Z"/>

      <!-- tagline ribbon -->
      <polygon class="fill-white" points="100,549 122,522 680,522 658,549 676,576 100,576 118,549"/>
      <text class="display-type tagline" x="390" y="566" text-anchor="middle">DESIGN &amp; BUILDER</text>

      <!-- location -->
      <circle class="fill-yellow" cx="405" cy="628" r="27"/>
      <path class="fill-black" d="M405 610 a12 12 0 0 1 12 12 c0 10 -12 22 -12 22 c0 0 -12 -12 -12 -22 a12 12 0 0 1 12 -12 Z"/>
      <circle class="fill-yellow" cx="405" cy="622" r="4.5"/>
      <text class="body-type address-line" x="405" y="700" text-anchor="middle">1840 Harbor View Rd., Ste. 310</text>
      <text class="body-type address-line" x="405" y="745" text-anchor="middle">Coral Bay, FL 33190</text>

      <!-- email -->
      <circle class="fill-yellow" cx="405" cy="798" r="27"/>
      <rect x="391" y="788" width="28" height="20" rx="2" fill="none" stroke="var(--sign-black)" stroke-width="3"/>
      <path d="M391 789 L405 800 L419 789 M391 807 L401 798 M419 807 L409 798" fill="none" stroke="var(--sign-black)" stroke-width="2.5"/>
      <text class="body-type email-line" x="405" y="860" text-anchor="middle">nolan@krtconstruction.com</text>

      <!-- office line -->
      <rect class="fill-yellow" x="300" y="905" width="412" height="72" rx="12"/>
      <rect class="fill-white" x="65" y="905" width="250" height="72" rx="12"/>
      <text class="body-type office-label" x="92" y="957">OFFICE</text>
      <circle class="fill-black" cx="308" cy="941" r="31" stroke="var(--sign-white)" stroke-width="3"/>
      <path d="M296 928 c-3 3 -4 8 0 15 c4 8 10 13 17 15 c4 1 7 -1 9 -4 l-6 -6 l-5 3 c-4 -2 -8 -6 -10 -11 l3 -5 Z" fill="var(--sign-white)"/>
      <text class="body-type office-number" x="347" y="961" textLength="343" lengthAdjust="spacingAndGlyphs">555.210.4470</text>

      <!-- mobile line -->
      <circle class="fill-yellow" cx="110" cy="1050" r="33"/>
      <path d="M96 1034 c-4 4 -5 10 0 19 c5 10 12 16 21 19 c5 1 9 -1 11 -5 l-8 -8 l-6 4 c-5 -3 -10 -8 -12 -14 l4 -6 Z" fill="var(--sign-black)"/>
      <text class="body-type mobile-number" x="160" y="1083" textLength="555" lengthAdjust="spacingAndGlyphs">555.308.2916</text>
    </svg>
  </main>
</body>
</html>
```